Veltrane Group Business Card Design

The CEO is looking for a new trendy look for his business card.
You can stay with current branding or come up with something new/creative. It can be 3D, including Medical Office buildings. You can use our logo in a variety of colors. Please include name, title, company name, company website, email address, cell number

Target Market(s)

Real Estate Development and Construction

Industry/Entity Type

Health care real estate

Contact Information for Business Card

Rohesh Kamdar, CEO M-604.781.2249 E-roheshkamdar@veltrane.com Address:4180 Lindqvist Ave, Brenford, OH 33482 www.veltrane.com

Font styles to use
Other font styles liked:
• Be creative

Requirements
Must have
• Creative, trendy look
Nice to have
• Please go to our website to get a feel- www. veltrane.com
Should not have
• small fonts

```html
<!DOCTYPE html>
<html lang="en">
<head>
<meta charset="UTF-8">
<title>Veltrane Group Business Card</title>
<link href="https://fonts.googleapis.com/css2?family=Poppins:wght@400;600;800&display=swap" rel="stylesheet">
<style>
  :root {
    --red: #b21f2b;
    --navy: #1e3354;
    --grey: #dcdcdc;
    --white: #ffffff;
    --backdrop: #1b1b1b;
  }
  * { box-sizing: border-box; margin: 0; padding: 0; }
  html, body {
    width: 1200px; height: 900px; overflow: hidden;
    background: var(--backdrop);
    font-family: "Poppins", sans-serif;
  }
  .stage {
    width: 1200px; height: 900px;
    display: flex; flex-direction: column;
    align-items: center; justify-content: center; gap: 44px;
  }
  .card {
    width: 630px; height: 360px;
    position: relative; overflow: hidden;
    box-shadow: 0 10px 30px rgba(0,0,0,.5);
  }
  /* Front */
  .card-front {
    background: var(--red);
    display: flex; align-items: center; justify-content: center;
  }
  .brand-name {
    font-weight: 800; letter-spacing: -1px; line-height: 1;
  }
  .card-front .brand-name { color: var(--white); font-size: 70px; }
  /* Back */
  .card-back { display: flex; flex-direction: column; }
  .band-top {
    background: var(--grey); height: 150px;
    display: flex; align-items: center; justify-content: center;
  }
  .card-back .brand-name { color: var(--red); font-size: 60px; }
  .band-mid {
    background: var(--red); height: 142px;
    display: flex; align-items: center; justify-content: center;
    color: var(--white); padding: 0 30px;
  }
  .identity { text-align: right; padding-right: 26px; }
  .person-name { font-weight: 600; font-size: 23px; letter-spacing: .5px; text-transform: uppercase; white-space: nowrap; }
  .person-title { font-weight: 400; font-size: 19px; margin-top: 2px; }
  .divider { width: 2px; height: 86px; background: var(--white); }
  .contact-list { list-style: none; padding-left: 26px; font-size: 17px; line-height: 1.5; }
  .contact-list li { display: flex; align-items: center; gap: 10px; white-space: nowrap; }
  .contact-list svg { width: 17px; height: 17px; flex: none; }
  .band-bottom {
    background: var(--navy); flex: 1;
    display: flex; align-items: center; padding-left: 70px;
    color: var(--white); font-size: 18px;
  }
</style>
</head>
<body>
<main class="stage">
  <section class="card card-front">
    <span class="brand-name">Veltrane Group</span>
  </section>

  <section class="card card-back">
    <div class="band-top">
      <span class="brand-name">Veltrane Group</span>
    </div>
    <div class="band-mid">
      <div class="identity">
        <p class="person-name">Rohesh Kamdar</p>
        <p class="person-title">CEO</p>
      </div>
      <div class="divider"></div>
      <ul class="contact-list">
        <li>
          <svg viewBox="0 0 24 24" fill="none" stroke="currentColor" stroke-width="2"><path d="M5 3h4l2 5-2.5 1.5a11 11 0 0 0 6 6L16 13l5 2v4a2 2 0 0 1-2 2A17 17 0 0 1 3 5a2 2 0 0 1 2-2z"/></svg>
          604.781.2249
        </li>
        <li>
          <svg viewBox="0 0 24 24" fill="none" stroke="currentColor" stroke-width="2"><rect x="2" y="5" width="20" height="14"/><path d="M2 5l10 8 10-8"/></svg>
          roheshkamdar@veltrane.com
        </li>
        <li>
          <svg viewBox="0 0 24 24" fill="none" stroke="currentColor" stroke-width="2"><circle cx="12" cy="12" r="10"/><path d="M2 12h20M12 2c3 3 3 17 0 20M12 2c-3 3-3 17 0 20"/></svg>
          www.veltrane.com
        </li>
      </ul>
    </div>
    <div class="band-bottom">
      <p class="address">4180 Lindqvist Ave, Brenford, OH 33482</p>
    </div>
  </section>
</main>
</body>
</html>
```